Corvane Capital Business Cards

These are professional business cards that are for my family office.
Put fake emails and phone numbers as of now until I finalize those components. This family office controls my families investments, assets, and future. The cards should be professional.
..
.
.
.
I just uploaded another variation of a logo I would like to see as a business card to I am inbeteen which logo to use

Target Market(s)

business

Industry/Entity Type

business

Contact Information for Business Card

Professional, wealth related, finance related.

Requirements
Must have
• Logo

```html
<!DOCTYPE html>
<html lang="en">
<head>
<meta charset="utf-8">
<title>Corvane Capital Business Cards</title>
<link rel="stylesheet" href="https://fonts.googleapis.com/css2?family=Cinzel:wght@600&family=Poppins:wght@400&display=swap">
<style>
  :root {
    --backdrop: #858585;
    --paper: #ffffff;
    --navy: #1b1f2c;
    --ink: #1f2230;
    --rule: #9a9a9a;
    --card-shadow: rgba(0, 0, 0, 0.55);
  }
  * { margin: 0; padding: 0; box-sizing: border-box; }
  html, body {
    width: 1093px;
    height: 1200px;
    overflow: hidden;
    background: var(--backdrop);
  }
  .card {
    position: absolute;
    left: 265px;
    width: 580px;
    height: 356px;
    border-radius: 24px;
    box-shadow: 3px 4px 4px var(--card-shadow);
  }
  .card--front { top: 226px; background: var(--paper); }
  .card--back { top: 621px; background: var(--navy); }

  .brand-mark {
    position: absolute;
    border-radius: 50%;
  }
  .card--front .brand-mark {
    left: 94px; top: 99px; width: 122px; height: 122px;
    border: 3px solid var(--navy);
  }
  .card--back .brand-mark {
    left: 208px; top: 70px; width: 166px; height: 166px;
    border: 3px solid var(--paper);
  }
  .brand-name {
    position: absolute;
    font-family: "Cinzel", serif;
    font-weight: 600;
    white-space: nowrap;
    letter-spacing: 0.5px;
  }
  .card--front .brand-name {
    left: 0; width: 310px; top: 220px;
    text-align: center;
    font-size: 26px;
    color: var(--navy);
  }
  .card--back .brand-name {
    left: 0; width: 582px; top: 250px;
    text-align: center;
    font-size: 36px;
    color: var(--paper);
  }

  .divider {
    position: absolute;
    left: 289px; top: 74px;
    width: 1px; height: 210px;
    background: linear-gradient(to bottom, transparent, var(--rule) 20%, var(--rule) 80%, transparent);
  }
  .details {
    position: absolute;
    left: 311px; top: 88px;
    color: var(--ink);
    font-family: "Poppins", sans-serif;
  }
  .person-name {
    font-family: "Cinzel", serif;
    font-weight: 600;
    font-size: 23px;
    line-height: 26px;
    color: var(--navy);
  }
  .person-title {
    font-size: 16px;
    line-height: 18px;
    margin-top: -3px;
  }
  .contact-list {
    list-style: none;
    margin-top: 14px;
  }
  .contact-list li {
    display: flex;
    align-items: center;
    font-size: 16px;
    line-height: 21px;
  }
  .contact-list svg {
    width: 15px; height: 15px;
    margin-right: 8px;
    fill: none;
    stroke: var(--ink);
    stroke-width: 1.6;
  }
  .address {
    font-style: normal;
    font-size: 16px;
    line-height: 21px;
    margin-top: 13px;
  }
</style>
</head>
<body>
  <section class="card card--front">
    <div class="brand-mark"></div>
    <div class="brand-name">Corvane Capital</div>
    <div class="divider"></div>
    <div class="details">
      <h1 class="person-name">DANIEL MERCER</h1>
      <p class="person-title">Managing Director</p>
      <ul class="contact-list">
        <li>
          <svg viewBox="0 0 16 16" aria-hidden="true"><path d="M4 1.5l2.2 3-1.4 1.6c.8 1.9 2.2 3.3 4.1 4.1l1.6-1.4 3 2.2-1.3 2.5C7.6 13.5 2.5 8.4 1.5 3z"/></svg>
          055-210 734 618
        </li>
        <li>
          <svg viewBox="0 0 16 16" aria-hidden="true"><rect x="1" y="3" width="14" height="10"/><path d="M1 3l7 6 7-6"/></svg>
          office@corvanemail.com
        </li>
        <li>
          <svg viewBox="0 0 16 16" aria-hidden="true"><circle cx="8" cy="8" r="6.5"/><ellipse cx="8" cy="8" rx="3" ry="6.5"/><path d="M1.5 8h13M2.5 4.8h11M2.5 11.2h11"/></svg>
          www.corvanecap.com
        </li>
      </ul>
      <address class="address">87, Harbor Row Suite 4<br>30118,Stellamark</address>
    </div>
  </section>

  <section class="card card--back">
    <div class="brand-mark"></div>
    <div class="brand-name">Corvane Capital</div>
  </section>
</body>
</html>
```